Varlomatch E-commerce Website Design

I'm looking into having my e-comm website built. We are an investment company that is investing in a private label focused on a rising sport category called Pickleball in EU market.

We will provide top quality material and acessories for players be ready to go to courts. We will have a range of: Rackets, Set of balls, Net, Lines, overgrip, water bottle, player bag.

As it´s a new sports category we would like to see an architecture that alows us to share some storytelling about the category, the brand and lead to purchase of our products.

We will position our self as an inclusive and fun brand that you can reach out to find more info about Pickleball Sport, buy your pickleball stuff and have fun. Its all about action and fun.

Target Market(s)

Europe Market

Industry/Entity Type

Pickleball (Sports)

Coding

Coded - Design and coding required

Number of Pages Required

1 page

Requirements
Must have
• E-commerce look and feel
Nice to have
• A bit of storytelling about the brand and specially the category (Pickleball).

```html
<!DOCTYPE html>
<html lang="en">
<head>
<meta charset="utf-8">
<title>Varlomatch – Pickleball Store</title>
<link href="https://fonts.googleapis.com/css2?family=Poppins:ital,wght@0,400;0,500;0,600;0,700;1,700;1,800&display=swap" rel="stylesheet">
<style>
:root{
  --green:#1d8556;
  --green-dark:#187048;
  --mint:#b2ddd0;
  --pale:#dfeaf2;
  --ink:#1e1e1e;
  --muted:#555;
  --line:#d9d9d9;
  --hero-a:#3f5f4a;
  --hero-b:#2b3f56;
  --steel:#3d7fa0;
}
*{box-sizing:border-box;margin:0;padding:0}
html,body{width:1200px;height:3559px;overflow:hidden}
body{font-family:'Poppins',sans-serif;color:var(--ink);background:#fff;position:relative}
.abs{position:absolute}
.btn{position:absolute;display:flex;align-items:center;justify-content:center;border-radius:24px;font-weight:600;font-size:16px;letter-spacing:1px;text-transform:uppercase}
.btn-fill{background:var(--green);color:#fff}
.btn-line{border:1.5px solid var(--green);color:var(--green);background:#fff}
.section-title{position:absolute;left:0;width:1200px;text-align:center;font-size:34px;font-weight:600}
.underline{position:absolute;left:577px;width:46px;height:3px;background:var(--green)}
.ph{position:absolute}

/* top bar */
.topbar{top:0;left:0;width:1200px;height:38px;background:var(--pale);font-size:13px;font-weight:500}
.topbar span{position:absolute;top:10px}
/* nav */
.nav{top:38px;left:0;width:1200px;height:79px;background:#fff}
.logo{position:absolute;left:67px;top:24px;font-size:25px;font-weight:700;color:var(--green);letter-spacing:.5px}
.menu a{position:absolute;top:30px;font-size:15px;font-weight:500;color:var(--ink);text-decoration:none}
/* hero */
.hero{top:117px;left:0;width:1200px;height:514px;background:linear-gradient(160deg,var(--hero-a),#4c6a52 45%,var(--hero-b))}
.welcome{position:absolute;left:488px;top:70px;width:238px;height:52px;background:var(--steel);color:#fff;font-size:32px;font-weight:500;text-align:center;line-height:52px}
.hero-title{position:absolute;left:0;width:1200px;top:128px;text-align:center;color:#fff;font-size:76px;font-weight:800;font-style:italic}
.dots span{position:absolute;top:485px;width:10px;height:10px;border-radius:50%;background:#3a7a58}
/* search */
.search{top:631px;left:0;width:1200px;height:101px;border-bottom:1px solid var(--line)}
.select{position:absolute;top:28px;width:199px;height:46px;border:1.5px solid #c8c8c8;border-radius:24px;font-size:14px;font-weight:500;padding:12px 20px}
.select svg{position:absolute;right:20px;top:18px}
/* products */
.prod{position:absolute;top:913px;width:229px}
.prod .img{height:217px;position:relative}
.tag{position:absolute;left:0;bottom:0;padding:3px 8px;font-size:16px;color:#fff;background:rgba(60,140,80,.85)}
.prod .name{margin-top:26px;font-size:16px;padding-left:2px}
.prod .price{margin-top:8px;font-size:16px;font-weight:600}
.prod .icons{margin-top:12px;display:flex;gap:36px}
/* featured */
.band{top:1413px;left:0;width:1200px;height:337px;background:var(--mint)}
.fcard{position:absolute;top:1581px;width:230px;height:268px;background:#fff;box-shadow:0 3px 8px rgba(0,0,0,.15)}
.fcard .img{height:216px}
.fcard p{text-align:center;font-size:16px;font-weight:500;margin-top:14px}
/* about */
.about-h{left:601px;top:2148px;width:500px;font-size:22px;font-weight:600;line-height:28px}
.about-p{left:601px;top:2214px;width:478px;font-size:15.5px;line-height:25.7px;color:#222}
/* testimonials */
.tcard{position:absolute;top:2777px;width:469px;height:350px;border:1px solid var(--line);background:#fff}
.avatar{position:absolute;left:26px;top:20px;width:109px;height:109px;border-radius:50%;background:linear-gradient(160deg,#c9d8e6,#8fb0cf)}
.stars{position:absolute;left:26px;top:145px;display:flex;gap:4px}
.ago{position:absolute;right:26px;top:148px;font-size:16px;color:#444}
.tq{position:absolute;left:26px;top:188px;width:430px;font-size:15.5px;line-height:24px}
.tq b{font-weight:600;display:block;margin-bottom:4px}
.tn{position:absolute;left:32px;top:300px;font-size:16px;font-weight:600}
.tdots span{position:absolute;top:2735px;width:11px;height:11px;border-radius:50%}
/* footer */
.footer{top:3194px;left:0;width:1200px;height:365px;background:var(--pale)}
.flogo{position:absolute;left:53px;top:88px;font-size:27px;font-weight:700;color:var(--green)}
.fcontact{position:absolute;left:53px;font-size:14px;font-weight:500;display:flex;gap:12px;align-items:flex-start;line-height:20px}
.col{position:absolute;top:86px}
.col h4{font-size:22px;font-weight:500;color:var(--green);margin-bottom:8px}
.col a{display:block;font-size:14px;color:var(--ink);text-decoration:none;line-height:34px}
.social span{position:absolute;top:3481px;width:46px;height:46px;border-radius:50%}
.copy{position:absolute;left:0;width:1090px;text-align:center;top:3527px;font-size:12px}
.news{top:3194px;left:887px;width:313px;height:365px;background:var(--green);color:#fff}
.news h3{position:absolute;left:30px;top:82px;font-size:26px;font-weight:500}
.news p{position:absolute;left:30px;top:128px;width:260px;font-size:14px;line-height:21px}
.email{position:absolute;left:31px;top:174px;width:250px;height:43px;border-radius:22px;background:#fff;color:#777;font-size:14px;padding:12px 22px}
.sub{position:absolute;left:137px;top:259px;width:143px;height:43px;border:1.5px solid #fff;border-radius:22px;font-size:15px;font-weight:500;display:flex;align-items:center;justify-content:center}
</style>
</head>
<body>

<header class="abs topbar">
  <span style="left:67px">FAQ</span>
  <span style="left:120px">Our Team</span>
  <span style="left:453px">Free Shipping Worldwide over $ 100 (EU, AU and all)</span>
  <span style="left:1043px">$ USD
    <svg width="10" height="7" viewBox="0 0 10 7"><path d="M1 1l4 4 4-4" stroke="#222" stroke-width="1.5" fill="none"/></svg></span>
  <svg class="abs" style="left:1116px;top:10px" width="17" height="17" viewBox="0 0 17 17"><circle cx="7" cy="7" r="5.5" stroke="#222" stroke-width="1.6" fill="none"/><path d="M11 11l4.5 4.5" stroke="#222" stroke-width="1.6"/></svg>
</header>

<nav class="abs nav">
  <div class="logo">VARLOMATCH</div>
  <div class="menu">
    <a style="left:343px;text-decoration:underline">Home</a>
    <a style="left:441px">About</a>
    <a style="left:541px">Products</a>
    <a style="left:660px">Testimonials</a>
    <a style="left:804px">Contact us</a>
  </div>
  <svg class="abs" style="left:1041px;top:28px" width="20" height="20" viewBox="0 0 20 20"><circle cx="8" cy="6" r="4" stroke="#333" stroke-width="1.5" fill="none"/><path d="M1 18c0-4 3-6 7-6s7 2 7 6z" stroke="#333" stroke-width="1.5" fill="none"/><path d="M15 6h4M17 4v4" stroke="#333" stroke-width="1.5"/></svg>
  <svg class="abs" style="left:1077px;top:29px" width="20" height="18" viewBox="0 0 20 18"><path d="M10 17S1 11 1 5.5A4.5 4.5 0 0 1 10 3a4.5 4.5 0 0 1 9 2.5C19 11 10 17 10 17z" stroke="#333" stroke-width="1.5" fill="none"/></svg>
  <svg class="abs" style="left:1113px;top:28px" width="20" height="20" viewBox="0 0 20 20"><path d="M1 2h3l2.5 11h10L19 5H5.5" stroke="#333" stroke-width="1.5" fill="none"/><circle cx="8" cy="17" r="1.5" fill="#333"/><circle cx="15" cy="17" r="1.5" fill="#333"/></svg>
</nav>

<section class="abs hero">
  <div class="ph" role="img" aria-label="Photo of players in a doubles pickleball match at the net" style="inset:0;background:linear-gradient(180deg,rgba(60,90,70,.2),rgba(40,50,90,.35))"></div>
  <svg class="abs" style="left:35px;top:218px" width="14" height="22" viewBox="0 0 14 22"><path d="M11 2L3 11l8 9" stroke="#cfd8cf" stroke-width="2" fill="none"/></svg>
  <svg class="abs" style="left:1148px;top:218px" width="14" height="22" viewBox="0 0 14 22"><path d="M3 2l8 9-8 9" stroke="#cfd8cf" stroke-width="2" fill="none"/></svg>
  <div class="welcome">Welcome to</div>
  <h1 class="hero-title">Varlomatch</h1>
  <div class="btn btn-fill" style="left:510px;top:257px;width:173px;height:46px">Shop Now</div>
  <div class="dots">
    <span style="left:555px;background:#28a06a"></span><span style="left:581px"></span><span style="left:607px"></span><span style="left:633px"></span>
  </div>
</section>

<section class="abs search">
  <div class="select" style="left:184px">Category...<svg width="10" height="7" viewBox="0 0 10 7"><path d="M1 1l4 4 4-4" stroke="#222" stroke-width="1.6" fill="none"/></svg></div>
  <div class="select" style="left:409px">Select...<svg width="10" height="7" viewBox="0 0 10 7"><path d="M1 1l4 4 4-4" stroke="#222" stroke-width="1.6" fill="none"/></svg></div>
  <div class="select" style="left:634px">Select...<svg width="10" height="7" viewBox="0 0 10 7"><path d="M1 1l4 4 4-4" stroke="#222" stroke-width="1.6" fill="none"/></svg></div>
  <div class="btn btn-fill" style="left:863px;top:28px;width:157px;height:46px">Search</div>
</section>

<h2 class="section-title" style="top:791px">New Products</h2>
<div class="underline" style="top:846px"></div>

<article class="prod" style="left:112px">
  <div class="img" role="img" aria-label="Pickleball paddle and ball on a green court" style="background:linear-gradient(135deg,#2f3a48 0 40%,#2f7a4a 60%)"><span class="tag">Trending</span></div>
  <p class="name">Pickleball Rackets</p><p class="price">$ 120.00</p>
  <div class="icons"><svg width="18" height="16" viewBox="0 0 20 18"><path d="M10 17S1 11 1 5.5A4.5 4.5 0 0 1 10 3a4.5 4.5 0 0 1 9 2.5C19 11 10 17 10 17z" stroke="#444" stroke-width="1.5" fill="none"/></svg><svg width="18" height="18" viewBox="0 0 20 20"><path d="M1 2h3l2.5 11h10L19 5H5.5" stroke="#444" stroke-width="1.5" fill="none"/><circle cx="8" cy="17" r="1.5" fill="#444"/><circle cx="15" cy="17" r="1.5" fill="#444"/></svg></div>
</article>
<article class="prod" style="left:360px">
  <div class="img" role="img" aria-label="Yellow and pink pickleballs on a court" style="background:linear-gradient(160deg,#7fa0c4,#c9b04a 50%,#c84a7a)"><span class="tag">Hot Sale</span></div>
  <p class="name">Set of balls</p><p class="price">$ 45.00</p>
  <div class="icons"><svg width="18" height="16" viewBox="0 0 20 18"><path d="M10 17S1 11 1 5.5A4.5 4.5 0 0 1 10 3a4.5 4.5 0 0 1 9 2.5C19 11 10 17 10 17z" stroke="#444" stroke-width="1.5" fill="none"/></svg><svg width="18" height="18" viewBox="0 0 20 20"><path d="M1 2h3l2.5 11h10L19 5H5.5" stroke="#444" stroke-width="1.5" fill="none"/><circle cx="8" cy="17" r="1.5" fill="#444"/><circle cx="15" cy="17" r="1.5" fill="#444"/></svg></div>
</article>
<article class="prod" style="left:609px">
  <div class="img" role="img" aria-label="Pickleball net across a dark court" style="background:linear-gradient(170deg,#7aa070,#3e4a63 45%,#2c3448)"><span class="tag">Trending</span></div>
  <p class="name">Pickleball Net</p><p class="price">$ 199.00</p>
  <div class="icons"><svg width="18" height="16" viewBox="0 0 20 18"><path d="M10 17S1 11 1 5.5A4.5 4.5 0 0 1 10 3a4.5 4.5 0 0 1 9 2.5C19 11 10 17 10 17z" stroke="#444" stroke-width="1.5" fill="none"/></svg><svg width="18" height="18" viewBox="0 0 20 20"><path d="M1 2h3l2.5 11h10L19 5H5.5" stroke="#444" stroke-width="1.5" fill="none"/><circle cx="8" cy="17" r="1.5" fill="#444"/><circle cx="15" cy="17" r="1.5" fill="#444"/></svg></div>
</article>
<article class="prod" style="left:858px">
  <div class="img" role="img" aria-label="Blue court with white lines" style="background:linear-gradient(170deg,#6fa87a,#3e7cc0 35%,#2f6fb8 80%,#8db070)"><span class="tag">Hot Sale</span></div>
  <p class="name">Lines</p><p class="price">$ 149.00</p>
  <div class="icons"><svg width="18" height="16" viewBox="0 0 20 18"><path d="M10 17S1 11 1 5.5A4.5 4.5 0 0 1 10 3a4.5 4.5 0 0 1 9 2.5C19 11 10 17 10 17z" stroke="#444" stroke-width="1.5" fill="none"/></svg><svg width="18" height="18" viewBox="0 0 20 20"><path d="M1 2h3l2.5 11h10L19 5H5.5" stroke="#444" stroke-width="1.5" fill="none"/><circle cx="8" cy="17" r="1.5" fill="#444"/><circle cx="15" cy="17" r="1.5" fill="#444"/></svg></div>
</article>

<div class="btn btn-line" style="left:519px;top:1287px;width:159px;height:46px">Shop All</div>

<section class="abs band"></section>
<h2 class="section-title" style="top:1476px">Featured Products</h2>
<div class="underline" style="top:1532px"></div>

<article class="fcard" style="left:110px"><div class="img" role="img" aria-label="Hand holding a white overgrip handle" style="background:linear-gradient(135deg,#c9603a,#e8c8b8 50%,#f2f2f0)"></div><p>Overgrip</p></article>
<article class="fcard" style="left:360px"><div class="img" role="img" aria-label="Yellow player bag" style="background:linear-gradient(120deg,#c8d4e0,#e2d21a 35%,#d4c010)"></div><p>Player bag</p></article>
<article class="fcard" style="left:612px"><div class="img" role="img" aria-label="Blue water bottle on a court" style="background:linear-gradient(180deg,#dfe6ea,#2a9ed0 50%,#6a5a4a)"></div><p>Water bottle</p></article>
<article class="fcard" style="left:862px"><div class="img" role="img" aria-label="Blue paddle set with yellow balls" style="background:linear-gradient(135deg,#b9cf8a 0 30%,#4a78d6 40%,#2c4e8a 70%,#a9c27a)"></div><p>Racket Set</p></article>

<div class="btn btn-fill" style="left:519px;top:1889px;width:159px;height:46px">View All</div>

<h2 class="section-title" style="top:2048px">About Pickleball</h2>
<div class="underline" style="top:2104px"></div>
<div class="ph" role="img" aria-label="Player reaching for a low shot at the net" style="left:112px;top:2152px;width:449px;height:371px;background:linear-gradient(180deg,#7f9aa8,#6a8a6a 40%,#a05a50 75%,#8a4a44);box-shadow:0 2px 6px rgba(0,0,0,.2)"></div>
<h3 class="abs about-h">Pickleball is growing internationally as well, with many European and Asian countries</h3>
<p class="abs about-p">Lorem Ipsum is simply dummy text of the printing and typesetting industry. Lorem Ipsum has been the industry's standard dummy text ever since the 1500s, when an unknown printer took a galley of type and scrambled it to make a type specimen book. It has survived not only five centuries, but also the leap into electronic typesetting, remaining essentially unchanged. It was popularised in the 1960s with the release of Letraset sheets containing Lorem Ipsum passages, and more recently.</p>
<div class="btn btn-fill" style="left:601px;top:2477px;width:157px;height:45px">Read More</div>

<h2 class="section-title" style="top:2673px">Testimonials</h2>
<div class="underline" style="top:2729px"></div>
<div class="tdots"><span style="left:1023px;background:var(--green)"></span><span style="left:1049px;background:#8fc9b2"></span><span style="left:1075px;background:#8fc9b2"></span></div>

<article class="tcard" style="left:116px">
  <div class="avatar" role="img" aria-label="Customer portrait"></div>
  <div class="stars"><svg width="136" height="24" viewBox="0 0 136 24"><g fill="#1d8556"><path id="st" d="M12 1l3.3 7 7.7.8-5.8 5.1 1.7 7.6L12 17.6 5.1 21.5l1.7-7.6L1 8.8l7.7-.8z"/><use href="#st" x="28"/><use href="#st" x="56"/><use href="#st" x="84"/><use href="#st" x="112"/></g></svg></div>
  <span class="ago">07 hours ago</span>
  <p class="tq"><b>@ Lorem Ipsum is simply dummy text, IDN RS</b>“It was popularised in the 1960s with the release of Letraset sheets containing Lorem Ipsum passages, and more recently with desktop publishing software”</p>
  <span class="tn">- Mara Tilden</span>
</article>
<article class="tcard" style="left:615px">
  <div class="avatar" role="img" aria-label="Customer portrait"></div>
  <div class="stars"><svg width="136" height="24" viewBox="0 0 136 24"><g fill="#1d8556"><use href="#st"/><use href="#st" x="28"/><use href="#st" x="56"/><use href="#st" x="84"/><use href="#st" x="112"/></g></svg></div>
  <span class="ago">09 hours ago</span>
  <p class="tq"><b>@ Lorem Ipsum is simply dummy text, IDN RS</b>“It was popularised in the 1960s with the release of Letraset sheets containing Lorem Ipsum passages, and more recently with desktop publishing software”</p>
  <span class="tn">- Oskar B</span>
</article>

<footer class="abs footer">
  <div class="flogo">VARLOMATCH</div>
  <div class="fcontact" style="top:136px"><svg width="14" height="20" viewBox="0 0 14 20"><path d="M7 19S1 11 1 7a6 6 0 0 1 12 0c0 4-6 12-6 12z" fill="#1d8556"/><circle cx="7" cy="7" r="2.3" fill="#dfeaf2"/></svg><span>218 Harbor Lane, Port Elm,<br>NA 40512</span></div>
  <div class="fcontact" style="top:199px"><svg width="17" height="13" viewBox="0 0 17 13"><rect width="17" height="13" rx="1.5" fill="#1d8556"/><path d="M1 1.5l7.5 6 7.5-6" stroke="#dfeaf2" stroke-width="1.4" fill="none"/></svg><span>info@varlomatch.eu</span></div>
  <div class="fcontact" style="top:236px"><svg width="16" height="17" viewBox="0 0 16 17"><path d="M3 1l3 3.5-2 2.2c1 2.4 3 4.4 5.4 5.4l2.1-2 3.5 3-1.6 2.6C7 15.5.5 9 1 2.5z" fill="#1d8556"/></svg><span>+1-555-204-3198</span></div>
  <div class="col" style="left:312px"><h4>Quick Links</h4><a>About</a><a>New Products</a><a>Featured Products</a><a>Testimonials</a><a>Contact us</a></div>
  <div class="col" style="left:500px"><h4>Support</h4><a>FAQ</a><a>Help &amp; Support</a><a>Gallery</a><a>Terms &amp; Conditions</a><a>Privacy Policy</a></div>
  <div class="col" style="left:694px"><h4>Explore</h4><a>Blogs</a><a>Gallery</a><a>Site Map</a><a>Our Team</a><a>Payment Methods</a></div>
</footer>
<div class="social">
  <span role="img" aria-label="Social link" style="left:55px;background:#3a5a9a"></span>
  <span role="img" aria-label="Social link" style="left:125px;background:#d8456a"></span>
  <span role="img" aria-label="Social link" style="left:195px;background:#1da1f2"></span>
</div>
<p class="copy">Copyright © 2023 Varlomatch. All Rights Reserved</p>

<aside class="abs news">
  <h3>Newsletter</h3>
  <p>Get Latest News and Updates and More Offers!</p>
  <div class="email">Your Email Address</div>
  <div class="sub">SUBSCRIBE</div>
</aside>

</body>
</html>
```